National online rug retailer needs a home page design

See the FloorNest logo and create a home page design around that color theme. Details are spelled out in word document uploaded below.

Apparently this website did not take my attachement showing the logo and basic requirements.  If you would send me your email address, I will send you the attachment directly.
Best regards,
Tom Vance
tvance@mrdcorp.example

Target Market(s)

The target market is home owners 25 to 75 years old with combined incomes over $100,000 per year.

Industry/Entity Type

Online

Requirements
Must have
• Lots of white space with black letters and creative use of red and possibly one other color. Would like a compelling call to action button.

```html
<!DOCTYPE html>
<html lang="en">
<head>
<meta charset="utf-8">
<title>FloorNest — Area Rugs</title>
<link href="https://fonts.googleapis.com/css2?family=Open+Sans:wght@400;600;700&display=swap" rel="stylesheet">
<style>
:root{
  --red:#d41f26;
  --ink:#222;
  --muted:#555;
  --line:#d8d8d8;
  --page:#eeeeee;
  --panel:#f2f2f2;
  --grey-head:#9a9a9a;
  --bar:#c9c9c9;
}
*{box-sizing:border-box;margin:0;padding:0}
html,body{width:880px;height:1200px;overflow:hidden}
body{background:var(--page);font-family:"Open Sans",Arial,sans-serif;color:var(--ink);position:relative}
.sheet{position:absolute;left:132px;top:0;width:616px;height:1200px;background:#fff}
.abs{position:absolute}
.cart{left:558px;top:4px;width:94px;height:16px;border:1px solid var(--line);font-size:7px;line-height:14px;padding-left:20px;color:var(--muted)}
.cart b{color:var(--red);font-weight:400}
.cart svg{position:absolute;left:8px;top:4px}
.toplinks{right:140px;top:8px;font-size:6px;color:var(--ink)}
.logo{left:146px;top:16px;width:150px;height:54px;background:#fafafa;border:1px solid #eee;padding:6px 4px}
.logo .name{font-size:20px;font-weight:600;color:var(--red);letter-spacing:-.5px;display:flex;align-items:center;gap:4px;white-space:nowrap}
.logo .name i{display:inline-block;width:9px;height:9px;background:var(--red)}
.logo .tag{font-size:6px;color:var(--muted);text-align:right;margin-top:2px}
.search{left:321px;top:46px;display:flex;height:16px;border:1px solid var(--line)}
.search span{width:146px;font-size:6px;color:#999;line-height:14px;padding-left:7px}
.search b{width:38px;background:#555;color:#fff;font-size:7px;font-weight:400;text-align:center;line-height:14px}
.toll{right:142px;top:33px;font-size:11px;font-weight:600;color:#444;display:flex;align-items:center;gap:6px;white-space:nowrap}
.toll em{font-style:normal;color:var(--red)}
.account{right:145px;top:64px;font-size:6px;color:var(--ink);white-space:nowrap}
.nav{left:138px;top:86px;width:604px;height:21px;background:var(--red);display:flex;justify-content:space-around;align-items:center;color:#fff;font-size:7.5px}
.side{left:138px;top:116px;width:136px}
.side .head{height:21px;background:var(--grey-head);color:#fff;font-size:7px;line-height:21px;padding-left:9px}
.side .group{height:22px;background:var(--panel);margin-top:2px;display:flex;justify-content:space-between;align-items:center;padding:0 7px 0 9px;font-size:7px;font-weight:700;color:var(--red)}
.side .group small{font-size:5px;font-weight:400;color:var(--muted)}
.side ul{list-style:none;padding:6px 0 4px 11px;font-size:7px;color:#333}
.side li{line-height:14.5px}
.side li:before{content:"›";margin-right:4px;color:#888}
.banner{left:293px;top:116px;width:449px;height:222px;background:linear-gradient(135deg,#8a8578 0%,#c9bfae 45%,#d8cfc0 70%,#b9ae9c 100%)}
.banner .big{position:absolute;left:24px;top:78px;color:#fff;font-size:40px;font-weight:400;line-height:1}
.banner .sub{position:absolute;left:24px;top:130px;color:#fff;font-size:23px;line-height:1}
.banner .caption{position:absolute;left:0;bottom:0;width:100%;height:40px;background:rgba(40,40,40,.65);color:#fff;font-size:13.5px;line-height:40px;padding-left:17px}
.banner .arrows{position:absolute;right:8px;bottom:12px;display:flex;gap:3px}
.section-title{left:303px;top:351px;font-size:8px;color:var(--red)}
.tile{width:103px;height:112px;border:1px solid var(--line);background:#fff}
.tile .ph{position:absolute;left:6px;top:6px;width:91px;height:81px}
.tile p{position:absolute;left:0;top:94px;width:100%;text-align:center;font-size:7px;color:#333}
.pager{top:986px;left:326px;display:flex;align-items:center;gap:6px}
.pager span{width:19px;height:16px;border:1px solid #555;font-size:8px;color:var(--red);text-align:center;line-height:14px;text-decoration:underline}
.pager span.plain{color:#333;text-decoration:none}
.pager i{font-style:normal;font-size:8px;color:#555;margin:0 -3px}
.also{left:630px;top:346px;width:111px;height:21px;background:var(--grey-head);color:#fff;font-size:7px;line-height:21px;padding-left:9px}
.nudge{width:13px;height:9px;background:#ddd;left:678px}
.pick{left:631px;width:110px;height:78px;border:1px solid var(--line)}
.pick .ph{position:absolute;left:5px;top:6px;width:99px;height:65px}
.pick-label{left:633px;font-size:7px;color:var(--red)}
.footer{left:138px;top:1025px;width:604px;height:145px;background:linear-gradient(#e4e4e4,#f6f6f6 30%,#fafafa)}
.paybox{left:148px;width:238px;background:#fff;border:1px solid var(--line);display:flex;align-items:center;justify-content:space-around;padding:0 6px}
.card{width:30px;height:19px;border:1px solid #ccc;font-size:6px;font-weight:600;color:#333;text-align:center;line-height:17px}
.col{top:1039px;font-size:6px;color:#333}
.col h4{font-size:7px;font-weight:400;color:var(--red);margin-bottom:5px}
.col li{list-style:none;line-height:11.3px}
.col li:before{content:"›";margin-right:4px;color:#999}
.bottom{left:138px;top:1170px;width:604px;height:24px;background:var(--bar);font-size:6px;color:#333;display:flex;justify-content:space-between;align-items:center;padding:0 8px}
.social{display:flex;align-items:center;gap:4px}
.social i{width:14px;height:14px;border-radius:50%;background:#2f7fc1;display:inline-block}
</style>
</head>
<body>
<div class="sheet"></div>

<div class="abs cart"><svg width="8" height="7" viewBox="0 0 8 7"><path d="M0 0h1.5l1 4h4.5l1-3H2.2" fill="none" stroke="#555" stroke-width=".8"/><circle cx="3" cy="6" r=".8" fill="#555"/><circle cx="6.5" cy="6" r=".8" fill="#555"/></svg>Items : <b>Total $0.00</b></div>
<div class="abs toplinks">VIEW CART &nbsp;| &nbsp;CHECKOUT</div>

<div class="abs logo"><div class="name"><i></i>FloorNest.com</div><div class="tag">for domestic and heirloom values</div></div>

<div class="abs search"><span>enter key words or item #</span><b>Search</b></div>

<div class="abs toll"><svg width="16" height="20" viewBox="0 0 16 20"><path d="M3 10a5 5 0 0 1 10 0" fill="none" stroke="#444" stroke-width="1.6"/><rect x="1.5" y="9" width="3.5" height="6" rx="1" fill="#444"/><rect x="11" y="9" width="3.5" height="6" rx="1" fill="#444"/><path d="M3 15q0 4 5 4" fill="none" stroke="#444"/></svg>Order toll Free : <em>1-888-555-0142</em></div>
<div class="abs account">MY ACCOUNT &nbsp; | &nbsp; SIGN IN &nbsp; | &nbsp; LIVE CHAT &nbsp; | &nbsp; ONLINE</div>

<nav class="abs nav"><span>HOME</span><span>SELECTION GUIDES</span><span>RUG CARE</span><span>FAQ</span><span>RETURN POLICY</span><span>FREE SHIPPING</span><span>CLEARANCE RUGS</span></nav>

<aside class="abs side">
  <div class="head">CATEGORIES</div>
  <div class="group">Rug Theme<small>[-] SHOW LESS</small></div>
  <ul><li>Traditional</li><li>Transitional</li><li>Casual</li></ul>
  <div class="group">Color Way<small>[-] SHOW LESS</small></div>
  <ul><li>Black</li><li>Blue</li><li>Green</li><li>Gold</li></ul>
  <div class="group">Size<small>[+] SHOW MORE</small></div>
  <div class="group">Shape<small>[+] SHOW MORE</small></div>
  <div class="group">Fiber Content<small>[+] SHOW MORE</small></div>
  <div class="group">MFGR. Brand<small>[+] SHOW MORE</small></div>
  <div class="group">MFGR.Collection<small>[+] SHOW MORE</small></div>
  <div class="group">Price<small>[+] SHOW MORE</small></div>
</aside>

<div class="abs banner" role="img" aria-label="Beige area rug with circular dot pattern in a living room">
  <div class="big">20%</div>
  <div class="sub">OFFER FOR SHIPPING</div>
  <div class="caption">Free Shipping-Risk Free in home trial-100% Price Match</div>
  <div class="arrows"><svg width="12" height="12"><circle cx="6" cy="6" r="5" fill="none" stroke="#ccc"/><path d="M7 3.5L4.5 6 7 8.5" fill="none" stroke="#ccc"/></svg><svg width="12" height="12"><circle cx="6" cy="6" r="5" fill="none" stroke="#ccc"/><path d="M5 3.5L7.5 6 5 8.5" fill="none" stroke="#ccc"/></svg></div>
</div>

<div class="abs section-title">SHOP FOR AREA RUGS BY STYLE</div>

<div class="abs tile" style="left:293px;top:378px"><div class="ph" role="img" aria-label="Purple geometric rug" style="background:linear-gradient(135deg,#6b3a8c,#9a5ab8)"></div><p>TRADITIONAL RUGS</p></div>
<div class="abs tile" style="left:402px;top:378px"><div class="ph" role="img" aria-label="Round medallion rug" style="background:radial-gradient(#c49478,#8a5a44)"></div><p>TRADITIONAL RUGS</p></div>
<div class="abs tile" style="left:510px;top:378px"><div class="ph" role="img" aria-label="Cream shag rug" style="background:#e2dccf"></div><p>TRADITIONAL RUGS</p></div>

<div class="abs tile" style="left:293px;top:498px"><div class="ph" role="img" aria-label="White shag rug beside armchair" style="background:linear-gradient(#c9b99a,#ece9e2)"></div><p>TRADITIONAL RUGS</p></div>
<div class="abs tile" style="left:402px;top:498px"><div class="ph" role="img" aria-label="Bordered rug with ivory field" style="background:radial-gradient(#efe4c8 45%,#3a2420 70%)"></div><p>TRADITIONAL RUGS</p></div>
<div class="abs tile" style="left:510px;top:498px"><div class="ph" role="img" aria-label="Floral rug in dining room" style="background:linear-gradient(#8a6a4a,#d97aa0)"></div><p>TRADITIONAL RUGS</p></div>

<div class="abs tile" style="left:293px;top:618px"><div class="ph" role="img" aria-label="Black and cream swirl rug in living room" style="background:linear-gradient(#9c8a6a,#2a2520)"></div><p>TRADITIONAL RUGS</p></div>
<div class="abs tile" style="left:402px;top:618px"><div class="ph" role="img" aria-label="Stacked patterned rugs" style="background:linear-gradient(135deg,#b8a88a,#6e6458)"></div><p>TRADITIONAL RUGS</p></div>
<div class="abs tile" style="left:510px;top:618px"><div class="ph" role="img" aria-label="Folded brown rugs" style="background:linear-gradient(#ffffff 30%,#b0764a)"></div><p>TRADITIONAL RUGS</p></div>

<div class="abs tile" style="left:293px;top:738px"><div class="ph" role="img" aria-label="Bedroom with patterned rug" style="background:linear-gradient(#6a3a28,#d6c8b4)"></div><p>TRADITIONAL RUGS</p></div>
<div class="abs tile" style="left:402px;top:738px"><div class="ph" role="img" aria-label="Jute rug texture" style="background:#9e7a5a"></div><p>TRADITIONAL RUGS</p></div>
<div class="abs tile" style="left:510px;top:738px"><div class="ph" role="img" aria-label="Beige block rug in lounge" style="background:linear-gradient(#a8a090,#e2d8c4)"></div><p>TRADITIONAL RUGS</p></div>

<div class="abs tile" style="left:293px;top:858px"><div class="ph" role="img" aria-label="Tan shag rug in sunny room" style="background:linear-gradient(#e0d6c4,#a88a66)"></div><p>TRADITIONAL RUGS</p></div>
<div class="abs tile" style="left:402px;top:858px"><div class="ph" role="img" aria-label="Brown woven rug" style="background:#7a5a44"></div><p>TRADITIONAL RUGS</p></div>
<div class="abs tile" style="left:510px;top:858px"><div class="ph" role="img" aria-label="Grey dotted rug" style="background:linear-gradient(#eae6e0,#a8a29a)"></div><p>TRADITIONAL RUGS</p></div>

<div class="abs pager"><span class="plain">«</span><span class="plain">1</span><span>2</span><span>3</span><span>4</span><span>5</span><span>6</span><span>7</span><i>...</i><span>15</span><span>16</span><span>»</span></div>

<div class="abs also">YOU MAY ALSO LIKE</div>
<svg class="abs nudge" style="top:377px" viewBox="0 0 13 9"><path d="M3.5 6l3-3 3 3" fill="none" stroke="#999"/></svg>

<div class="abs pick" style="top:394px"><div class="ph" role="img" aria-label="Cream floral rug" style="background:linear-gradient(135deg,#efe0c4,#d9a070)"></div></div>
<div class="abs pick-label" style="top:478px">MARLA VESPER RUG</div>
<div class="abs pick" style="top:495px"><div class="ph" role="img" aria-label="Red traditional rug" style="background:#a8503a"></div></div>
<div class="abs pick-label" style="top:580px">MARLA VESPER RUG</div>
<div class="abs pick" style="top:596px"><div class="ph" role="img" aria-label="Brown leaf pattern rug" style="background:linear-gradient(135deg,#5a3a22,#c8b890)"></div></div>
<div class="abs pick-label" style="top:680px">MARLA VESPER RUG</div>
<div class="abs pick" style="top:696px"><div class="ph" role="img" aria-label="Circle pattern rug in room" style="background:linear-gradient(#3a3a3a,#c8c0b0)"></div></div>
<div class="abs pick-label" style="top:780px">MARLA VESPER RUG</div>
<div class="abs pick" style="top:795px"><div class="ph" role="img" aria-label="Wave stripe rug" style="background:linear-gradient(#8a8a8a,#e0d8c8 50%,#b8642e)"></div></div>
<div class="abs pick-label" style="top:879px">MARLA VESPER RUG</div>
<div class="abs pick" style="top:894px"><div class="ph" role="img" aria-label="Rust and grey floral rug" style="background:linear-gradient(135deg,#c8784a,#9a9aa8)"></div></div>
<div class="abs pick-label" style="top:978px">MARLA VESPER RUG</div>
<svg class="abs nudge" style="top:997px" viewBox="0 0 13 9"><path d="M3.5 3l3 3 3-3" fill="none" stroke="#999"/></svg>

<footer class="abs footer"></footer>
<div class="abs paybox" style="top:1034px;height:38px">
  <span class="card">Zelvo</span><span class="card">Kardin</span><span class="card">Trelpa</span><span class="card">Avexa</span><span class="card">Quillo</span><span class="card">Brevin</span>
</div>
<div class="abs paybox" style="top:1079px;height:41px">
  <svg width="30" height="30"><circle cx="15" cy="15" r="13" fill="#e0c060"/></svg>
  <svg width="30" height="30"><circle cx="15" cy="15" r="13" fill="#e8c030"/></svg>
  <svg width="44" height="18"><rect width="44" height="18" rx="2" fill="#d8d8d8"/></svg>
  <svg width="44" height="18"><rect width="44" height="18" rx="2" fill="#1d4f8c"/></svg>
  <svg width="36" height="18"><rect width="36" height="18" rx="2" fill="#c8d0c4"/></svg>
</div>

<div class="abs col" style="left:415px"><h4>CUSTOMER SERVICE</h4><ul><li>Shipping</li><li>Return Policy</li><li>Privacy Policy</li><li>Ordering &amp; Delivery Checklist</li><li>Terms of Use</li><li>Terms of Sale</li><li>Contact Us</li><li>Environmental Policy</li></ul></div>
<div class="abs col" style="left:535px"><h4>RESOURCES</h4><ul><li>Product Articles</li><li>Learning Center</li><li>Help</li><li>Refer A Friend</li><li>FloorNest Blog</li><li>Room Scene Viewer</li><li>Site Map</li><li>FAQ</li><li>Customer Testimonials</li><li>Photo Gallery</li></ul></div>
<div class="abs col" style="left:648px"><h4>CORPORATE INFO</h4><ul><li>About FloorNest.com</li><li>Careers</li><li>Affiliates</li></ul></div>

<div class="abs bottom"><span>Copyright 2013.FloorNest. All rights reserved.</span><span class="social">Follow us : <i></i><i></i><i></i></span></div>
</body>
</html>
```